Bold, Modern, Clean "Kestrelwaymassage.com" website

Why we stand out?
We are a male and female mobile massage team. Our names are Paul and Lina. 
Kestrel Way is a Seattle based mobile massage service. Our massage is offered to the community with a goal of facilitating balance within each individual. We specialize in integrated Pain management, and sports/medical massage therapy. Every client's first assessment is attended by our male and female massage therapist team. Depending on the goals identified for an individual determines which therapist will be assigned to provide treatment, if not both.

Our passion...
Here at Kestrel Way, we have a great passion for Postural Resoration and how it is integrated into an individual's Massage treatment. We pride ourselves in being natural facilitators of healing, which takes the ego of the therapist out of the client's healing process. We strive to deliver the best massage possible by including modalities such as Neuromuscular, Myofascial release, spontaneous muscle release, postural restoration, orthopedic, and medical massage.

Our education...

We are both Graduates of Venmora, school of massage therapy. We have continuing education in medical massage, myofacial release, trigger point therapy, postural restoration, anatomy, and spontaneous muscle release. Lina is also a Certified Yoga Instructor, which amplifies her experience with flexibility and strength as it pertains to each individual. Paul's passion is Massage, stretching, and strength training to encourage postural restoration and realignment.

Our rates-

Our rates are $75/ 60 minutes, $95/ 90 minutes, and $120/ 120 minutes.

Education-
Both Lina and I worked as behavioral health professionals that specialized in life skills mentoring for youth who had experienced different types of trauma. This led us both to want to help others in a different environment, where individuals can be empowered to take responsibility over their own healing. To us, massage is a type of manipulation physical therapy, that encourages healing on many levels.

Advice to any massage client-
The most important thing to 'us', as Licenced providers is to get you on to our table to show you our skills. But a good therapist never forgets that it's not about what we do for you, but what we can facilitate for you. Your health and healing has nothing to do with us. It is yours, not ours. Identify what your goals are with any Therapist, and know what the end looks like. Progress should be tangible, such as range of motion, and decreased pain.

Lina and Paul at Kestrel Way are awesome! I recently had open heart surgery, and Lina worked on me to increase my range of motion while helping with the pinched nerve from my arm being in the same position for so long during my surgery. My wife drives a lot for work, and Paul has helped decrease her neck and lower back pain immensely. They are seriously the best therapists I have ever worked with. I would recommend them to anyone who needs anything from stress relief to a medical massage treatment. They are professional, up beat, easy going, and always on time. And, I love that they meet us where ever we like! We did a staycation recently, where they came to our hotel to give us relaxation massages. Although usually they come to our home, where we focus on pain related issues. We will continue to work with them for a long, long time.

Target Market(s)

Mobile massage therapy clients

Industry/Entity Type

Massage Therapy

Coding

Coded - Design and coding required

Number of Pages Required

1 page

Font styles to use
Serif
Sans Serif

Requirements
Must have
• Please add or remove any information that would help the presentation of our website. Our logo is posted below, please include into the website.
• Please include a contact field that includes, kestrelwaymassage@fernmail.net,
• (206) 555-0148
• We have also included our own stock photos, as well as a photo of Paul and Lina. Please include a cropped photo of both massage therapists.

```html
<!DOCTYPE html>
<html lang="en">
<head>
<meta charset="utf-8">
<title>Kestrel Way Mobile Massage</title>
<link href="https://fonts.googleapis.com/css2?family=Open+Sans:wght@400;600;700&family=Roboto+Condensed:wght@400;700&display=swap" rel="stylesheet">
<style>
:root{
  --navy:#1b2a72;
  --navy-deep:#131d55;
  --blue:#1e88e5;
  --blue-light:#42a5f5;
  --sky:#e8f3fd;
  --ink:#4a4f5c;
  --muted:#8a8f99;
  --white:#ffffff;
}
*{box-sizing:border-box;margin:0;padding:0}
html,body{width:690px;height:1200px;overflow:hidden;background:var(--white)}
body{position:relative;font-family:"Open Sans",sans-serif;color:var(--ink);font-size:8px;line-height:1.45}
.abs{position:absolute}

/* header */
.brand{left:22px;top:12px;display:flex;align-items:center;gap:7px;font-family:"Roboto Condensed",sans-serif;font-weight:700;font-size:17px;line-height:1;color:var(--navy);text-transform:uppercase;white-space:nowrap}
.brand .dot{width:18px;height:18px;border-radius:50%;background:var(--blue)}
.top-contact{right:22px;top:2px;text-align:right;color:var(--navy);font-family:"Roboto Condensed",sans-serif;line-height:1.1}
.top-contact small{display:block;font-size:7px}
.top-contact strong{font-size:10px}
.main-nav{left:180px;top:24px;width:510px;height:22px;background:var(--navy);display:flex;align-items:center;padding-left:8px}
.main-nav a{color:var(--white);text-decoration:none;font-family:"Roboto Condensed",sans-serif;font-size:8.5px;padding:0 11px;line-height:22px}
.main-nav a.active{background:var(--blue)}

/* hero */
.hero{left:0;top:46px;width:690px;height:300px;background:linear-gradient(110deg,#5c4a3e 0%,#b88e74 35%,#e9d7c6 55%,#8a6e5c 80%,#3f3a40 100%)}
.hero-caption{right:40px;top:206px;width:230px;background:rgba(20,20,30,.78);padding:10px 14px 12px;color:var(--white)}
.hero-caption h2{font-family:"Roboto Condensed",sans-serif;font-size:15px;line-height:1.2;text-transform:uppercase;font-weight:700;margin-bottom:5px}
.hero-caption p{font-size:7px;color:#d7d9e0}
.dots{left:315px;top:330px;display:flex;gap:5px}
.dots span{width:7px;height:7px;border-radius:50%;background:rgba(255,255,255,.6)}
.dots span:first-child{background:var(--white)}

/* quick contact */
.quick{left:446px;top:318px;width:218px;height:212px;background:var(--blue);box-shadow:0 3px 8px rgba(0,0,0,.2);z-index:3}
.quick h3{background:var(--blue-light);color:var(--white);font-family:"Roboto Condensed",sans-serif;font-size:14px;padding:7px 12px;text-transform:uppercase}
.quick form{width:150px;margin:12px auto 0}
.quick .field{display:block;width:150px;height:15px;background:var(--white);border:none;margin-bottom:6px;font-size:6.5px;color:var(--muted);padding:2px 5px;font-family:"Open Sans",sans-serif}
.quick .submit{background:var(--navy);color:var(--white);border:none;font-family:"Roboto Condensed",sans-serif;font-size:9px;font-weight:700;padding:4px 12px;margin-top:2px}

/* info cards */
.info-card{top:352px;width:196px}
.info-card .photo{height:74px;background:linear-gradient(135deg,#c9a48a,#efe3d6 60%,#a1bfd6)}
.info-card h4{font-family:"Roboto Condensed",sans-serif;font-size:11px;color:var(--navy);text-transform:uppercase;margin:6px 0 2px;border-bottom:1px solid #d7dae2;padding-bottom:2px}
.info-card p{font-size:6.5px;color:var(--muted)}

/* why */
.why{left:30px;top:528px;width:430px}
.why h2{font-size:20px;color:var(--blue);font-weight:400;margin-bottom:8px}
.why p{font-size:6.8px;margin-bottom:5px}
.btn{display:inline-block;background:var(--navy);color:var(--white);font-size:6.5px;padding:4px 10px;font-weight:700;text-transform:uppercase;margin-top:4px}
.why-photo{left:490px;top:520px;width:150px;height:150px;border-radius:50%;background:radial-gradient(circle at 45% 45%,#d9b59a,#8d6a55 70%,#5a4a40);border:4px solid var(--sky)}

/* services band */
.band{left:0;top:680px;width:690px;height:180px}
.service{top:735px;width:186px;height:66px;background:var(--white);border-radius:33px;display:flex;align-items:center;padding:0 12px;gap:8px;box-shadow:0 2px 6px rgba(0,0,0,.15)}
.service .icon{flex:none;width:44px;height:44px;border-radius:50%;background:linear-gradient(135deg,#bfe0fa,#64b5f6)}
.service h5{font-size:8.5px;color:var(--navy);font-weight:700;margin-bottom:2px}
.service p{font-size:6.2px;color:var(--muted);line-height:1.35}

/* reviews & advice */
.reviews{left:30px;top:872px;width:300px}
.advice{left:365px;top:872px;width:300px}
.reviews h2,.advice h2{font-size:15px;color:var(--blue);font-weight:400;margin-bottom:8px}
.reviews p,.advice p{font-size:6.6px}
.author{font-weight:700;color:var(--navy);font-size:8px;margin-top:6px}
.stars{display:flex;gap:2px;margin-top:3px}
.advice-body{display:flex;gap:10px}
.advice-photo{flex:none;width:80px;height:80px;border-radius:50%;background:radial-gradient(circle at 40% 50%,#e0a58a,#b86a52 60%,#7a4d40)}

/* footer */
.footer{left:0;top:1042px;width:690px;height:136px;background:var(--navy)}
.footer-col{top:1058px;color:#c5cbe6}
.footer-col h6{color:var(--white);font-size:9px;font-weight:600;margin-bottom:5px}
.footer-col li{list-style:none;font-size:7px;margin-bottom:2px}
.footer-brand{left:560px;top:1096px;display:flex;align-items:center;gap:7px;font-family:"Roboto Condensed",sans-serif;font-weight:700;font-size:15px;line-height:1;color:var(--white);text-transform:uppercase;white-space:nowrap}
.footer-brand .dot{width:16px;height:16px;border-radius:50%;background:var(--blue)}
.copyright{left:0;top:1178px;width:690px;height:22px;background:var(--navy-deep);color:#9aa3cc;font-size:6.5px;padding:6px 30px}
</style>
</head>
<body>

<header>
  <div class="abs brand"><span class="dot"></span>Kestrel Way</div>
  <div class="abs top-contact"><small>Quick Contact</small><strong>(206) 555-0148</strong></div>
  <nav class="abs main-nav">
    <a class="active">HOME</a><a>ABOUT US</a><a>PRICES</a><a>EDUCATION</a><a>MASSAGE</a><a>REVIEW</a><a>CONTACT</a>
  </nav>
</header>

<section class="abs hero" role="img" aria-label="Therapist giving a sports massage to a client lying on a treatment table"></section>
<div class="abs hero-caption">
  <h2>Sports Therapy and Massage</h2>
  <p>Mobile sports massage brought to your door, focused on recovery, mobility and lasting relief.</p>
</div>
<div class="abs dots"><span></span><span></span><span></span><span></span></div>

<aside class="abs quick">
  <h3>Quick Contact</h3>
  <form>
    <input class="field" placeholder="Full Name">
    <input class="field" placeholder="Email address">
    <input class="field" placeholder="Phone no">
    <input class="field" placeholder="Location">
    <input class="field" placeholder="Type of Treatment">
    <button class="submit" type="button">SUBMIT</button>
  </form>
</aside>

<article class="abs info-card" style="left:30px">
  <div class="photo" role="img" aria-label="Therapist working on a client's shoulder"></div>
  <h4>About Us</h4>
  <p>We are a male and female mobile massage team serving Seattle with care.</p>
</article>
<article class="abs info-card" style="left:236px">
  <div class="photo" role="img" aria-label="Massage therapists in a training session"></div>
  <h4>Our Education</h4>
  <p>Graduates of Venmora with training in medical and myofascial massage work.</p>
</article>

<section class="abs why">
  <h2>Why we stand out?</h2>
  <p>We are a male and female mobile massage team. Our names are Paul and Lina. Kestrel Way is a Seattle based mobile massage service. Our massage is offered to the community with a goal of facilitating balance within each individual. We specialize in integrated Pain management, and sports/medical massage therapy.</p>
  <p>Every client's first assessment is attended by our male and female massage therapist team. Depending on the goals identified for an individual determines which therapist will be assigned to provide treatment, if not both.</p>
  <span class="btn">Read More</span>
</section>
<div class="abs why-photo" role="img" aria-label="Close-up of a back massage"></div>

<svg class="abs band" viewBox="0 0 690 180" preserveAspectRatio="none" aria-hidden="true">
  <defs><linearGradient id="bandFill" x1="0" y1="0" x2="1" y2="1"><stop offset="0" stop-color="#2f8fe6"/><stop offset="1" stop-color="#1565c0"/></linearGradient></defs>
  <path d="M0 30 C170 0 300 45 460 20 C560 5 630 10 690 25 L690 150 C560 180 420 140 260 165 C150 180 60 160 0 150 Z" fill="url(#bandFill)"/>
</svg>
<div class="abs service" style="left:40px">
  <div class="icon" role="img" aria-label="Sports therapy figure"></div>
  <div><h5>Sports Therapy</h5><p>Targeted work to aid recovery, speed healing and improve range of motion.</p></div>
</div>
<div class="abs service" style="left:252px">
  <div class="icon" role="img" aria-label="Body massage figure"></div>
  <div><h5>Body Massage</h5><p>Full body relaxation massage to ease stress and restore natural balance.</p></div>
</div>
<div class="abs service" style="left:464px">
  <div class="icon" role="img" aria-label="Pain management figure"></div>
  <div><h5>Pain management</h5><p>Integrated pain care using trigger point and postural restoration methods.</p></div>
</div>

<section class="abs reviews">
  <h2>Latest Reviews</h2>
  <p>Lina and Paul at Kestrel Way are awesome! I recently had open heart surgery, and Lina worked on me to increase my range of motion while helping with the pinched nerve from my arm being in the same position for so long during my surgery. My wife drives a lot for work, and Paul has helped decrease her neck and lower back pain immensely.</p>
  <div class="author">By Darcy T.</div>
  <div class="stars">
    <svg width="50" height="9" viewBox="0 0 50 9" aria-label="Five stars"><g fill="#f5b700"><polygon points="4.5,0 5.6,3.3 9,3.3 6.2,5.4 7.3,9 4.5,6.8 1.7,9 2.8,5.4 0,3.3 3.4,3.3"/><polygon transform="translate(10 0)" points="4.5,0 5.6,3.3 9,3.3 6.2,5.4 7.3,9 4.5,6.8 1.7,9 2.8,5.4 0,3.3 3.4,3.3"/><polygon transform="translate(20 0)" points="4.5,0 5.6,3.3 9,3.3 6.2,5.4 7.3,9 4.5,6.8 1.7,9 2.8,5.4 0,3.3 3.4,3.3"/><polygon transform="translate(30 0)" points="4.5,0 5.6,3.3 9,3.3 6.2,5.4 7.3,9 4.5,6.8 1.7,9 2.8,5.4 0,3.3 3.4,3.3"/><polygon transform="translate(40 0)" points="4.5,0 5.6,3.3 9,3.3 6.2,5.4 7.3,9 4.5,6.8 1.7,9 2.8,5.4 0,3.3 3.4,3.3"/></g></svg>
  </div>
</section>

<section class="abs advice">
  <h2>Advice to any massage client</h2>
  <div class="advice-body">
    <div class="advice-photo" role="img" aria-label="Diagram of neck and shoulder pain area"></div>
    <p>The most important thing to 'us', as Licenced providers is to get you on to our table to show you our skills. But a good therapist never forgets that it's not about what we do for you, but what we can facilitate for you. Your health and healing has nothing to do with us. It is yours, not ours.</p>
  </div>
</section>

<footer>
  <div class="abs footer"></div>
  <div class="abs footer-col" style="left:30px"><h6>Quick Links</h6><ul><li>About Us</li><li>Our Massage</li><li>Reviews</li><li>Why Us</li></ul></div>
  <div class="abs footer-col" style="left:150px"><h6>Services</h6><ul><li>Massage</li><li>Sports Therapy</li><li>Pain Management</li></ul></div>
  <div class="abs footer-col" style="left:270px"><h6>Resources</h6><ul><li>Testimonials</li><li>Our Education</li><li>Our Passion</li><li>Why we stand out?</li></ul></div>
  <div class="abs footer-col" style="left:400px;width:150px"><h6>Contact Info</h6><ul><li>820 Alder Court Suite 210,<br>Seattle, WA 98101</li><li>(206) 555-0148</li><li>kestrelwaymassage@fernmail.net</li></ul></div>
  <div class="abs footer-brand"><span class="dot"></span>Kestrel Way</div>
  <div class="abs copyright">© 2024 Kestrel Way. All rights reserved.</div>
</footer>

</body>
</html>
```